Employment Agency Website Design

We are working with an employment agency in California.

Some sites to use for content/competitors and inspiration:

https://www.pinecrestjobs.com/us/en
https://www.velmorusa.com
https://www.dravenworks.us
https://www.quillora.com/en
https://www.tomvalusa.com
https://www.fernstaffing.com

Thank you for taking the time to consider designing a website for us. We are web developers based in Stockton, CA, USA. Most of our projects go through the same process. Understanding this process may help you win a project with us. We custom-code all of our websites in-house. We don’t have any requirements as to what tools you use for your design, but we prefer Figma files. For any design that we label as four-stars, we send it to the client for review. The client picks the final design they want us to use. Once we complete this process, we will continue to show additional clients all the four-star sites and purchase them later. Your designs will have multiple chances to sell. For better chances of success, we ask that you follow these guidelines.

IMAGES:
If you use any images or icons in the design, we ask that you have a link to the asset so we can purchase the image/icon. Most of the designs we submit do not have the customer’s images on them unless they have some great images. Be creative; show us the feeling you are trying to portray with your image choices. Use any royalty-free site you choose. We subscribe to Adobe and mainly use their images, but we can purchase images outside of Adobe. PLEASE NOTE: we will not submit designs to clients with watermarks on the images.

FONTS:
We ask that you identify the fonts used in the design. This can be done in a message if you want. We typically use Google Fonts and Adobe Fonts.

CONTENT:
We're always open to different content and ideas. We often submit designs with stock images so the client can see our vision. We typically take pictures after the website launch to use their images with our vision. Lorem Ipsum is fine for paragraphs, but we ask that you write the headers in correct English. We want to be able to show the vision and identify the sections of the website.

INSPIRATION:
We typically add a couple of links in the brief of websites we like to help you get started in your design.

REVISIONS:
We do not often ask for revisions of the designs unless we see something in the design that may not appeal to the client. If there are slight changes that we want to make, we do that in the development process.

FEEDBACK:
We rarely give feedback on designs during the design process. We are working on many website projects and do not have the time to provide feedback. We usually respond if your request is well thought out and asks specific questions, but a note asking “feedback, please” usually goes unanswered.

```html
<!DOCTYPE html>
<html lang="en">
<head>
<meta charset="utf-8">
<title>Brightpath Talent — Employment Agency</title>
<link href="https://fonts.googleapis.com/css2?family=Lato:wght@300;400;700;900&display=swap" rel="stylesheet">
<style>
:root{
  --red:#d0313a;
  --red-dark:#b3262e;
  --black:#0d0d0d;
  --ink:#1b1b1b;
  --grey:#6c6c6c;
  --line:#cfcfcf;
  --white:#ffffff;
  --star:#f3a20f;
}
*{margin:0;padding:0;box-sizing:border-box}
html,body{width:1200px;height:3788px;overflow:hidden}
body{position:relative;font-family:'Lato',sans-serif;color:var(--ink);background:var(--white)}
.abs{position:absolute}
.btn{position:absolute;height:36px;line-height:36px;padding:0 22px;font-weight:700;font-size:15px;color:var(--white);clip-path:polygon(8px 0,calc(100% - 8px) 0,100% 50%,calc(100% - 8px) 100%,8px 100%,0 50%);white-space:nowrap}
.btn-red{background:var(--red)}
.btn-black{background:var(--black)}
.btn-white{background:var(--white);color:var(--red)}

/* header */
.top-line{left:0;top:0;width:1200px;height:4px;background:var(--red)}
.contact-tab{left:544px;top:0;width:541px;height:37px;background:var(--red);color:var(--white);font-size:13px;display:flex;align-items:center;justify-content:center;gap:26px;clip-path:polygon(0 0,100% 0,98% 100%,2% 100%)}
.contact-tab .dot{display:inline-block;width:9px;height:9px;background:var(--white);border-radius:2px;margin-right:8px;vertical-align:middle}
.brand{left:110px;top:30px;display:flex;align-items:center;gap:10px}
.brand-mark{width:30px;height:30px;background:var(--red);border-radius:50%}
.brand-name{font-size:34px;font-weight:700;color:var(--red);line-height:1}
.main-nav{left:488px;top:60px;display:flex;gap:47px;font-size:13.5px;font-weight:700;color:var(--ink)}
.search-icon{left:1074px;top:61px}

/* hero */
.hero{left:0;top:98px;width:1200px;height:525px;overflow:hidden}
.hero-left{position:absolute;left:0;top:0;width:640px;height:525px;background:linear-gradient(90deg,#4a3a2c 0%,#6b2a22 40%,#7a1d1b 100%)}
.hero-right{position:absolute;left:600px;top:0;width:600px;height:525px;background:linear-gradient(90deg,#2a2524 0%,#3f3a38 50%,#55504c 100%)}
.hero-label{font-size:23px;font-weight:700;color:var(--white);text-decoration:underline;text-underline-offset:5px}
.hero-title{font-size:68px;font-weight:700;color:var(--white);line-height:77px;letter-spacing:1px}
.hero-sub{font-size:18px;font-weight:700;color:var(--white)}

/* tabs */
.tab{position:absolute;top:709px;height:44px;line-height:44px;text-align:center;font-size:18px;color:#555;background:var(--white);box-shadow:0 3px 10px rgba(0,0,0,.08)}
.tab.active{background:var(--red);color:var(--white)}
.ind{position:absolute;width:303px;height:38px;border-bottom:1.5px solid var(--line);display:flex;align-items:center;font-size:14px;color:#555}
.ind-icon{width:22px;height:22px;border:1.5px solid #9a9a9a;border-radius:4px;margin-right:16px}
.ind-arrow{margin-left:auto}

/* about */
.section-title{font-size:44px;font-weight:900;color:var(--ink);display:flex;align-items:center;gap:20px;letter-spacing:.5px}
.section-title .light{font-weight:400}
.title-mark{width:32px;height:32px;background:var(--red);border-radius:50%}
.about-text{left:668px;top:1312px;width:430px;font-size:14.5px;line-height:28.6px;color:var(--grey)}

/* how it works */
.step-title{position:absolute;width:320px;text-align:center;font-size:18px;font-weight:700;color:var(--white);letter-spacing:.3px}
.step-text{position:absolute;width:300px;text-align:center;font-size:14px;line-height:26.5px;color:var(--white)}

/* testimonials */
.card{position:absolute;top:2812px;width:316px;height:380px;filter:drop-shadow(0 4px 14px rgba(0,0,0,.09))}
.card-body{width:100%;height:100%;background:var(--white);clip-path:polygon(0 3%,50% 0,100% 3%,100% 97%,50% 100%,0 97%);padding:42px 36px 0}
.person{display:flex;align-items:center;gap:20px}
.avatar{width:52px;height:52px;border-radius:50%;background:linear-gradient(135deg,#c9ccd2,#3b4b66)}
.person-name{font-size:14px;font-weight:700;color:#444}
.stars{color:var(--star);font-size:11px;letter-spacing:1px}
.quote{margin-top:22px;font-size:13.5px;line-height:26.2px;color:var(--grey)}

/* footer */
.footer-name{left:0;top:3552px;width:1200px;text-align:center;font-size:40px;font-weight:700;color:var(--white)}
.footer-nav{left:0;top:3636px;width:1200px;display:flex;justify-content:center;gap:66px;font-size:19px;font-weight:700;color:var(--white)}
.social{left:0;top:3692px;width:1200px;display:flex;justify-content:center;gap:17px}
.social span{width:33px;height:33px;background:var(--red);border-radius:50%}
.copyright{left:0;top:3748px;width:1200px;text-align:center;font-size:15px;color:var(--white)}
</style>
</head>
<body>

<!-- Header -->
<div class="abs top-line"></div>
<div class="abs contact-tab">
  <span><span class="dot"></span>info@brightpathtalent.com</span><span>|</span>
  <span><span class="dot"></span>+1 800 555 0142</span><span>|</span>
  <span><span class="dot"></span>Login/Sign Up</span>
</div>
<div class="abs brand"><span class="brand-mark"></span><span class="brand-name">Brightpath Talent</span></div>
<nav class="abs main-nav"><span>Find Jobs</span><span>Hire Talent</span><span>Explore Consulting Solutions</span><span>Discover Insights</span></nav>
<svg class="abs search-icon" width="14" height="14" viewBox="0 0 14 14"><circle cx="6" cy="6" r="4.2" fill="none" stroke="#1b1b1b" stroke-width="2"/><line x1="9" y1="9" x2="13" y2="13" stroke="#1b1b1b" stroke-width="2.2"/></svg>

<!-- Hero -->
<section class="abs hero">
  <div class="hero-left" role="img" aria-label="Smiling employer standing in a bright office, washed in deep red"></div>
  <div class="hero-right" role="img" aria-label="Job seeker with headphones working on a laptop at home"></div>
  <svg class="abs" style="left:0;top:0" width="1200" height="525" viewBox="0 0 1200 525">
    <polygon points="0,0 555,0 620,262 555,525 0,525" fill="rgba(120,24,22,.55)"/>
    <polygon points="555,0 570,0 635,262 570,525 555,525 620,262" fill="var(--red)"/>
  </svg>
  <div class="abs hero-label" style="left:441px;top:118px">EMPLOYER</div>
  <div class="abs hero-title" style="right:640px;top:156px;text-align:right">I AM AN<br>EMPLOYER</div>
  <div class="abs hero-sub" style="right:639px;top:318px">Make your workforce the best it can be</div>
  <div class="btn btn-black" style="left:244px;top:366px">Request Talent</div>
  <div class="btn btn-red" style="left:401px;top:366px">Staffing Solutions</div>

  <div class="abs hero-label" style="left:684px;top:118px">JOB SEEKER</div>
  <div class="abs hero-title" style="left:680px;top:156px">LOOKING<br>FOR A JOB</div>
  <div class="abs hero-sub" style="left:683px;top:318px">Sign up for the vacancies that best suit your profile</div>
  <div class="btn btn-red" style="left:685px;top:366px">Find A Job</div>
  <div class="btn btn-black" style="left:828px;top:366px">Search Here</div>
</section>

<!-- Job categories -->
<div class="tab active" style="left:147px;width:185px">Jobs by Industry</div>
<div class="tab" style="left:348px;width:186px">Jobs by State</div>
<div class="tab" style="left:553px;width:184px">Jobs by Type</div>
<div class="tab" style="left:754px;width:297px">Jobs by Featured Companies</div>

<div class="ind" style="left:103px;top:805px"><span class="ind-icon"></span>Accounting &amp; Finance<span class="ind-arrow">&#8594;</span></div>
<div class="ind" style="left:103px;top:874px"><span class="ind-icon"></span>Call Center &amp; Customer Service<span class="ind-arrow">&#8594;</span></div>
<div class="ind" style="left:103px;top:943px"><span class="ind-icon"></span>Creative &amp; Marketing<span class="ind-arrow">&#8594;</span></div>
<div class="ind" style="left:103px;top:1012px"><span class="ind-icon"></span>Engineering &amp; Technology<span class="ind-arrow">&#8594;</span></div>
<div class="ind" style="left:449px;top:805px"><span class="ind-icon"></span>Hospitality<span class="ind-arrow">&#8594;</span></div>
<div class="ind" style="left:449px;top:874px"><span class="ind-icon"></span>Human Resources<span class="ind-arrow">&#8594;</span></div>
<div class="ind" style="left:449px;top:943px"><span class="ind-icon"></span>Industrial &amp; Manufacturing<span class="ind-arrow">&#8594;</span></div>
<div class="ind" style="left:449px;top:1012px"><span class="ind-icon"></span>Medical &amp; Science<span class="ind-arrow">&#8594;</span></div>
<div class="ind" style="left:794px;top:805px"><span class="ind-icon"></span>Retail<span class="ind-arrow">&#8594;</span></div>
<div class="ind" style="left:794px;top:874px"><span class="ind-icon"></span>Transportation<span class="ind-arrow">&#8594;</span></div>
<div class="ind" style="left:794px;top:943px"><span class="ind-icon"></span>Warehousing<span class="ind-arrow">&#8594;</span></div>

<!-- About -->
<svg class="abs" style="left:112px;top:1200px" width="496" height="496" viewBox="0 0 496 496" role="img" aria-label="Team of three colleagues reviewing work on a laptop at night">
  <defs><linearGradient id="aboutPhoto" x1="0" y1="0" x2="1" y2="1"><stop offset="0" stop-color="#2b3442"/><stop offset=".55" stop-color="#5a4a44"/><stop offset="1" stop-color="#1c222c"/></linearGradient></defs>
  <polygon points="248,0 496,124 496,372 248,496 0,372 0,124" fill="var(--red)"/>
  <polygon points="248,20 476,134 476,362 248,476 20,362 20,134" fill="url(#aboutPhoto)"/>
</svg>
<h2 class="abs section-title" style="left:668px;top:1240px"><span class="title-mark"></span><span>ABOUT <span class="light">US</span></span></h2>
<div class="abs about-text">
  <p>At vero eos et accusamus et iusto odio dignissimos ducimus qui blanditiis praesentium voluptatum deleniti atque corrupti quos dolores et quas molestias excepturi sint occaecati cupiditate non provident, similique sunt in culpa qui officia deserunt mollitia animi, id est laborum et dolorum fuga. Et harum quidem rerum facilis est et expedita distinctio.</p>
  <p style="margin-top:28.6px">Nam libero tempore, cum soluta nobis est eligendi optio cumque nihil impedit quo minus id quod maxime placeat facere possimus, omnis voluptas assumenda est</p>
</div>
<div class="btn btn-red" style="left:668px;top:1616px">Read More</div>

<!-- How it works -->
<svg class="abs" style="left:0;top:1830px" width="1200" height="790" viewBox="0 0 1200 790" role="img" aria-label="Red band over a faint photo of an office team">
  <polygon points="0,126 1200,126 1200,670 600,790 0,670" fill="var(--red)"/>
  <polygon points="206,88 600,2 994,88 994,126 600,165 206,126" fill="var(--black)"/>
</svg>
<h2 class="abs section-title" style="left:412px;top:1890px;color:var(--white);gap:20px"><span class="title-mark"></span><span>HOW IT <span class="light">WORKS</span></span></h2>

<svg class="abs" style="left:0;top:2062px" width="1200" height="250" viewBox="0 0 1200 250">
  <defs>
    <linearGradient id="s1" x1="0" y1="0" x2="1" y2="1"><stop offset="0" stop-color="#c8c2bb"/><stop offset="1" stop-color="#3a3c44"/></linearGradient>
    <linearGradient id="s2" x1="0" y1="0" x2="1" y2="1"><stop offset="0" stop-color="#6d5a66"/><stop offset="1" stop-color="#2d3550"/></linearGradient>
    <linearGradient id="s3" x1="0" y1="0" x2="1" y2="1"><stop offset="0" stop-color="#8fa3b8"/><stop offset="1" stop-color="#5b6572"/></linearGradient>
  </defs>
  <g>
    <polygon points="266,2 380,58 380,172 266,228 152,172 152,58" fill="var(--black)"/>
    <polygon points="266,24 360,70 360,160 266,206 172,160 172,70" fill="url(#s1)" role="img" aria-label="Team planning around a desk"/>
    <polygon points="600,2 714,58 714,172 600,228 486,172 486,58" fill="var(--black)"/>
    <polygon points="600,24 694,70 694,160 600,206 506,160 506,70" fill="url(#s2)" role="img" aria-label="Candidate in a friendly interview"/>
    <polygon points="934,2 1048,58 1048,172 934,228 820,172 820,58" fill="var(--black)"/>
    <polygon points="934,24 1028,70 1028,160 934,206 840,160 840,70" fill="url(#s3)" role="img" aria-label="Recruiter shaking hands with a client"/>
  </g>
  <g fill="var(--black)">
    <circle cx="418" cy="111" r="10"/><polygon points="432,102 452,102 458,111 452,120 432,120"/>
    <circle cx="752" cy="111" r="10"/><polygon points="766,102 786,102 792,111 786,120 766,120"/>
  </g>
  <g fill="var(--white)">
    <polygon points="266,180 296,196 296,230 266,246 236,230 236,196"/>
    <polygon points="600,180 630,196 630,230 600,246 570,230 570,196"/>
    <polygon points="934,180 964,196 964,230 934,246 904,230 904,196"/>
  </g>
  <g fill="var(--red)" font-family="Lato,sans-serif" font-weight="900" font-size="30" text-anchor="middle">
    <text x="266" y="224">01</text><text x="600" y="224">02</text><text x="934" y="224">03</text>
  </g>
</svg>

<div class="step-title" style="left:106px;top:2323px">DESCRIBE YOUR NEED</div>
<div class="step-title" style="left:440px;top:2323px">VIEW MATCHING CANDIDATES</div>
<div class="step-title" style="left:774px;top:2323px">CONNECT WITH A RECRUITER</div>
<div class="step-text" style="left:116px;top:2353px">At vero eos et accusamus et iusto odio dignissimos ducimus qui blanditiis praesentium voluptatum deleniti atque corrupti</div>
<div class="step-text" style="left:450px;top:2353px">At vero eos et accusamus et iusto odio dignissimos ducimus qui blanditiis praesentium voluptatum deleniti atque corrupti</div>
<div class="step-text" style="left:784px;top:2353px">At vero eos et accusamus et iusto odio dignissimos ducimus qui blanditiis praesentium voluptatum deleniti atque corrupti</div>
<div class="btn btn-black" style="left:463px;top:2474px">Get A Quote</div>
<div class="btn btn-white" style="left:617px;top:2474px">Contact Us</div>

<!-- Testimonials -->
<h2 class="abs section-title" style="left:333px;top:2704px"><span class="title-mark"></span><span>OUR HAPPY <span class="light">CUSTOMERS</span></span></h2>

<div class="card" style="left:103px"><div class="card-body">
  <div class="person"><span class="avatar" role="img" aria-label="Customer portrait"></span><div><div class="person-name">Daniel Reyes</div><div class="stars">&#9733;&#9733;&#9733;&#9733;&#9734;</div></div></div>
  <p class="quote">I must explain to you how all this mistaken idea of denouncing pleasure and praising pain was born and I will give you a complete account of the system, and expound the actual teachings of the great explorer of the truth, the master-builder of human happiness. No one rejects, dislikes, or avoids pleasure itself, because it is pleasure</p>
</div></div>
<div class="card" style="left:441px"><div class="card-body">
  <div class="person"><span class="avatar" role="img" aria-label="Customer portrait"></span><div><div class="person-name">Daniel Reyes</div><div class="stars">&#9733;&#9733;&#9733;&#9733;&#9734;</div></div></div>
  <p class="quote">I must explain to you how all this mistaken idea of denouncing pleasure and praising pain was born and I will give you a complete account of the system, and expound the actual teachings of the great explorer of the truth, the master-builder of human happiness. No one rejects, dislikes, or avoids pleasure itself, because it is pleasure</p>
</div></div>
<div class="card" style="left:779px"><div class="card-body">
  <div class="person"><span class="avatar" role="img" aria-label="Customer portrait"></span><div><div class="person-name">Daniel Reyes</div><div class="stars">&#9733;&#9733;&#9733;&#9733;&#9734;</div></div></div>
  <p class="quote">I must explain to you how all this mistaken idea of denouncing pleasure and praising pain was born and I will give you a complete account of the system, and expound the actual teachings of the great explorer of the truth, the master-builder of human happiness. No one rejects, dislikes, or avoids pleasure itself, because it is pleasure</p>
</div></div>

<div class="btn btn-black" style="left:469px;top:3238px">View More</div>
<div class="btn btn-red" style="left:603px;top:3238px">Get Started</div>

<!-- Footer -->
<svg class="abs" style="left:0;top:3346px" width="1200" height="442" viewBox="0 0 1200 442" role="img" aria-label="Dark footer over a faint photo of a crowd">
  <defs><linearGradient id="foot" x1="0" y1="0" x2="0" y2="1"><stop offset="0" stop-color="#1a1a1a"/><stop offset="1" stop-color="#0b0b0b"/></linearGradient></defs>
  <polygon points="0,124 600,0 1200,124 1200,442 0,442" fill="url(#foot)"/>
</svg>
<div class="abs" style="left:570px;top:3460px;width:60px;height:60px;background:var(--red);border-radius:50%"></div>
<div class="abs footer-name">Brightpath Talent</div>
<nav class="abs footer-nav"><span>Find Jobs</span><span>Hire Talent</span><span>Explore Consulting Solutions</span><span>Discover Insights</span></nav>
<div class="abs social">
  <span role="img" aria-label="Social link 1"></span><span role="img" aria-label="Social link 2"></span><span role="img" aria-label="Social link 3"></span><span role="img" aria-label="Social link 4"></span><span role="img" aria-label="Social link 5"></span>
</div>
<div class="abs copyright">(C) Copyright 2024 | All Rights Reserved</div>

</body>
</html>
```